one side yoga classes, other side rental log cabin

I need a flyer to advertise yoga classes on a lake , and to describe the various styles of classes, and who they can benefit, Days Times .prices
Linked to it is a rental log cabin that can be rented privetly to families or Groups (8 max) www.kelverstonletsbay.com This also is rented to yoga teacher that would like to Hire Cabin and the Studio www.orvelinehaven.co.uk or
for Holistic weekends.

Teacher

```html
<!DOCTYPE html>
<html lang="en">
<head>
<meta charset="utf-8">
<title>Orveline Haven &amp; Kelverston Holidays – Lakeside Flyer</title>
<link rel="stylesheet" href="https://fonts.googleapis.com/css2?family=Fondamento&family=Dancing+Script:wght@700&family=Roboto:wght@400;700&family=Roboto+Condensed:wght@400&display=swap">
<style>
  :root{
    --backdrop:#2a2a2c;
    --plum-deep:#34123a;
    --plum-band:#6a2d68;
    --rule:#5e2f63;
    --ink:#2b1a2a;
    --headline:#2a1a20;
    --white:#ffffff;
    --sky-top:#f5eff7;
    --sky-mid:#ecd6e4;
    --glow:#f3d2b6;
    --sunset:#e8ad82;
    --shore:#b3a39f;
    --sea:#8c8590;
    --mint:#a9e2cf;
    --teal:#12ab9a;
    --teal-dark:#1f8c82;
    --teal-text:#7fc9bd;
    --taupe:#4a3d41;
    --taupe-light:#8d8185;
    --script-red:#d92a2a;
    --body-grey:#222222;
  }
  *{margin:0;padding:0;box-sizing:border-box}
  html,body{width:1200px;height:1015px;overflow:hidden;background:var(--backdrop)}
  .card{position:absolute;width:1134px;height:805px;overflow:hidden;transform:scale(.6);transform-origin:0 0;font-family:"Roboto",Arial,sans-serif}
  .card.yoga{left:260px;top:16px;background:var(--plum-deep);color:var(--ink)}
  .card.cabin{left:260px;top:515px;background:linear-gradient(180deg,var(--mint) 0%,var(--teal) 100%)}

  /* yoga side */
  .top-band{position:absolute;left:0;top:0;width:100%;height:28px;background:var(--plum-deep)}
  .photo{position:absolute;left:0;top:28px;width:100%;height:560px;
    background:
      radial-gradient(ellipse 360px 220px at 190px 440px, rgba(255,190,120,.75), rgba(255,190,120,0) 70%),
      linear-gradient(180deg,var(--sky-top) 0%,var(--sky-mid) 22%,var(--glow) 44%,var(--sunset) 62%,var(--shore) 80%,var(--sea) 100%)}
  .base-wave{position:absolute;left:0;top:0;width:1134px;height:805px}
  .headline{position:absolute;left:310px;top:52px;width:810px;text-align:center;font-family:"Fondamento",serif;font-weight:400;font-size:50px;line-height:68px;color:var(--headline)}
  .studio-band{position:absolute;left:213px;top:203px;width:921px;height:36px;
    background:linear-gradient(90deg,rgba(106,45,104,0) 0%,var(--plum-band) 14%,var(--plum-band) 100%)}
  .studio-band span{position:absolute;left:0;right:0;top:6px;text-align:center;color:var(--white);font-size:26px;line-height:1;padding-left:40px}
  .row{position:absolute;font-size:21px;line-height:1;white-space:nowrap;color:var(--ink)}
  .row b{font-weight:700;color:#2a1230}
  .row.lead{font-size:23px}
  .rule{position:absolute;height:1px;background:var(--rule)}
  .rule.tab{height:4px}
  .logo-name{position:absolute;left:56px;top:665px;width:324px;text-align:center;color:var(--white);font-size:34px;letter-spacing:6px;line-height:1;text-transform:uppercase}
  .divider{position:absolute;left:419px;top:603px;width:1px;height:153px;background:rgba(255,255,255,.25)}
  .contact{position:absolute;left:464px;color:var(--white);line-height:1;white-space:nowrap}
  .contact.name{top:597px;font-size:22px}
  .contact.address{top:629px;font-size:22px}
  .contact.phones{top:673px;font-family:"Roboto Condensed",Arial,sans-serif;font-size:48px}
  .contact.web{top:745px;font-size:22px;font-weight:700;letter-spacing:4.5px}

  /* cabin side */
  .cabin-band{position:absolute;left:26px;top:18px;width:1108px;height:159px;background:var(--taupe)}
  .cabin-sheet{position:absolute;left:26px;top:177px;width:1108px;height:423px;background:var(--white)}
  .cabin-photo{position:absolute;left:46px;top:197px;width:640px;height:383px;background:linear-gradient(180deg,#c9dfe6 0%,#a7b98f 55%,#6d5a44 100%)}
  .cabin-brand{position:absolute;right:30px;top:196px;font-family:"Dancing Script",cursive;font-weight:700;font-size:46px;line-height:1;color:var(--script-red);white-space:nowrap}
  .cabin-tagline{position:absolute;right:30px;top:262px;font-size:26px;line-height:1;color:var(--body-grey);white-space:nowrap}
  .vase{position:absolute;left:0;top:0;width:1134px;height:805px}
  .panel-text{position:absolute;left:735px;width:350px;text-align:center;font-size:20px;line-height:28px;color:var(--body-grey)}
  .panel-text.red{color:var(--script-red)}
  .panel-rule{position:absolute;left:830px;width:160px;height:1px;background:#bbb}
  .panel-rule.red{background:var(--script-red);width:100px;left:860px}
  .lodge-strip{position:absolute;left:26px;top:600px;width:760px;height:48px;background:var(--teal-dark)}
  .lodge-strip span{position:absolute;left:0;right:0;top:11px;text-align:center;color:var(--teal-text);font-size:26px;line-height:1}
  .lodge-box{position:absolute;left:26px;top:648px;width:760px;height:126px;background:linear-gradient(90deg,var(--taupe) 0%,var(--taupe-light) 100%)}
  .lodge-phones{position:absolute;left:0;right:0;top:22px;text-align:center;color:var(--white);font-size:36px;line-height:1}
  .lodge-web{position:absolute;left:0;right:0;top:78px;text-align:center;color:#1c1416;font-size:26px;letter-spacing:3.5px;line-height:1}
</style>
</head>
<body>
<section class="card yoga">
  <div class="photo" role="img" aria-label="Photograph of a woman silhouetted in tree pose on a beach at sunset, arms raised above her head"></div>
  <div class="top-band"></div>
  <svg class="base-wave" viewBox="0 0 1134 805" aria-hidden="true">
    <defs>
      <linearGradient id="plumFill" x1="0" y1="0" x2="1" y2="1">
        <stop offset="0" stop-color="#3a1541"/>
        <stop offset="1" stop-color="#4d2450"/>
      </linearGradient>
    </defs>
    <path d="M0,540 C260,585 620,578 1134,522 L1134,805 L0,805 Z" fill="url(#plumFill)"/>
  </svg>

  <h1 class="headline">A Peaceful &amp; Tranquil Lakeside<br>Retreat In The Heart Of Norfolk</h1>
  <div class="studio-band"><span>THE CALM AND RELAXING LAKESIDE STUDIO</span></div>

  <div class="row lead" style="left:373px;top:267px">One to One Bookings On Monday</div>
  <div class="rule" style="left:363px;top:305px;width:673px"></div>
  <div class="rule tab" style="left:363px;top:303px;width:121px"></div>
  <div class="row" style="left:373px;top:319px">TUESDAY :</div>
  <div class="row" style="left:497px;top:319px">8-9 Hatha Yoga (STARTING SOON)</div>
  <div class="row" style="left:497px;top:351px"><b>Gentle Asana Class</b></div>
  <div class="rule" style="left:498px;top:392px;width:538px"></div>
  <div class="row" style="left:497px;top:407px">10-11.15 <b>Dru Yoga</b></div>
  <div class="row" style="left:497px;top:462px">19.00-20.00 <b>Hatha Yoga</b> (Halbrook Memorial Hall)</div>
  <div class="rule" style="left:363px;top:496px;width:673px"></div>
  <div class="rule tab" style="left:363px;top:494px;width:121px"></div>
  <div class="row" style="left:373px;top:510px">FRIDAY</div>
  <div class="row" style="left:486px;top:510px">: 10.00-11.15 <b>Hatha Yoga</b></div>

  <div class="logo-name">Orveline</div>
  <div class="divider"></div>
  <div class="contact name">Orveline Haven</div>
  <div class="contact address">7 Marrowby Lakes, Marrowby. PE41 2QT</div>
  <div class="contact phones">01632 960 418 • 07700 900 362</div>
  <div class="contact web">www.orvelinehaven.co.uk</div>
</section>

<section class="card cabin">
  <div class="cabin-band"></div>
  <div class="cabin-sheet"></div>
  <div class="cabin-photo" role="img" aria-label="Photograph of the rental log cabin beside the lake"></div>
  <div class="cabin-brand">Kelverston Holidays</div>
  <div class="cabin-tagline">Your Lakeside Log Cabin Break!</div>

  <svg class="vase" viewBox="0 0 1134 805" aria-hidden="true">
    <path d="M760,350 C800,420 790,470 750,520 C720,560 730,600 760,640 C700,690 700,740 740,805 L1080,805 C1110,740 1110,690 1060,640 C1090,600 1100,560 1070,520 C1030,470 1020,420 1080,350 L1134,350 L1134,805 Z" fill="none"/>
    <path d="M740,805 C700,740 700,690 760,640 C730,600 720,560 750,520 C790,470 800,420 760,350 L1090,350 C1040,420 1050,470 1080,520 C1110,560 1100,600 1070,640 C1120,690 1120,740 1085,805 Z" fill="#f6f3f5" stroke="#a89ea3" stroke-width="8"/>
  </svg>

  <p class="panel-text" style="top:380px">Enjoy all the luxuries<br>of home with just so<br>much more comfort!</p>
  <div class="panel-rule" style="top:476px"></div>
  <p class="panel-text red" style="top:488px">Rent privately to<br>families or groups (8 max)</p>
  <div class="panel-rule" style="top:552px"></div>
  <p class="panel-text" style="top:562px">Holistic retreats for<br>any groups looking to<br>really relax and enjoy<br>a weekend of<br>meditation and yoga<br>in a studio suspended<br>over the lake itself</p>
  <div class="panel-rule red" style="top:768px"></div>

  <div class="lodge-strip"><span>For Lodge Availability, Contact Us Direct</span></div>
  <div class="lodge-box">
    <div class="lodge-phones">01632 960 418 • 07700 900 362</div>
    <div class="lodge-web">www.kelverstonletsbay.com</div>
  </div>
</section>
</body>
</html>
```